Our companies name is The Gilded Ladle and we specialize in craft cupcakes, what I mean by that is that we bake our cupcakes with craft beer and other alcoholic drinks. We are trying to focus on being elegant but at the same time unpretentious. Since we are incorporating beer in our cupcakes we want the business card to have our logo in the front and our information in the back.

Once we select the best design we will provide the contact information to be added. Thank you.

Industry/Entity Type

Business

Font styles to use
Decorative
Script

Requirements
Must have
• Round corners
Should not have
• Square corners

```html
<!DOCTYPE html>
<html lang="en">
<head>
<meta charset="utf-8">
<title>The Gilded Ladle – Business Card</title>
<link rel="stylesheet" href="https://fonts.googleapis.com/css2?family=Exo+2:wght@400;500;600&display=swap">
<style>
  :root {
    --backdrop: #a0a0a0;
    --card-white: #ffffff;
    --card-black: #0b0b0b;
    --card-black-glow: #2a2a2a;
    --ink: #111111;
    --ink-soft: #333333;
    --brand-teal: #6fc7bf;
    --brand-red: #e0262b;
  }
  * { box-sizing: border-box; margin: 0; padding: 0; }
  html, body {
    width: 1200px;
    height: 800px;
    overflow: hidden;
    background: var(--backdrop);
    font-family: "Exo 2", Arial, sans-serif;
  }
  .canvas {
    position: relative;
    width: 1200px;
    height: 800px;
    display: flex;
    align-items: center;
    justify-content: center;
    gap: 60px;
  }
  .card {
    position: relative;
    width: 500px;
    height: 286px;
    border-radius: 22px;
    overflow: hidden;
    box-shadow: 0 10px 24px rgba(0, 0, 0, 0.25);
  }
  /* Info side */
  .card--info {
    background: var(--card-white);
    color: var(--ink);
  }
  .info-block {
    position: absolute;
    left: 70px;
    top: 78px;
  }
  .holder-name {
    font-size: 44px;
    font-weight: 400;
    letter-spacing: 0.5px;
    line-height: 1;
    margin-bottom: 20px;
  }
  .contact-line {
    display: flex;
    align-items: center;
    gap: 10px;
    font-size: 16px;
    color: var(--ink-soft);
    line-height: 1.6;
  }
  .contact-line svg { width: 14px; height: 14px; flex: none; }
  .corner-mark {
    position: absolute;
    right: 22px;
    bottom: 20px;
    display: flex;
    align-items: center;
    gap: 8px;
  }
  .corner-mark .mark-dot {
    width: 14px;
    height: 14px;
    border-radius: 50%;
    background: var(--brand-red);
  }
  .corner-mark .mark-name {
    font-size: 15px;
    font-weight: 600;
    color: var(--ink);
  }
  /* Logo side */
  .card--logo {
    background: radial-gradient(circle at 50% 48%, var(--card-black-glow) 0%, var(--card-black) 62%);
    display: flex;
    align-items: center;
    justify-content: center;
    gap: 14px;
  }
  .card--logo .mark-dot {
    width: 26px;
    height: 26px;
    border-radius: 50%;
    background: var(--brand-red);
  }
  .card--logo .mark-name {
    font-size: 34px;
    font-weight: 600;
    color: var(--brand-teal);
    letter-spacing: 1px;
  }
</style>
</head>
<body>
<main class="canvas">
  <section class="card card--info" aria-label="Card back with contact details">
    <div class="info-block">
      <h1 class="holder-name">DanaReyes</h1>
      <p class="contact-line">
        <svg viewBox="0 0 14 14" aria-hidden="true"><path d="M3 1h2.5l1 3-1.5 1.2a7 7 0 0 0 3.8 3.8L10 7.5l3 1V11a2 2 0 0 1-2 2A10 10 0 0 1 1 3a2 2 0 0 1 2-2z" fill="#333"/></svg>
        thegildedladle@mailbox.example
      </p>
      <p class="contact-line">
        <svg viewBox="0 0 14 14" aria-hidden="true"><rect x="1" y="3" width="12" height="9" rx="1" fill="#333"/><path d="M1.5 3.5 7 8l5.5-4.5" stroke="#fff" stroke-width="1.2" fill="none"/></svg>
        555-214-0187
      </p>
    </div>
    <div class="corner-mark">
      <span class="mark-dot"></span>
      <span class="mark-name">The Gilded Ladle</span>
    </div>
  </section>

  <section class="card card--logo" aria-label="Card front with brand name">
    <span class="mark-dot"></span>
    <span class="mark-name">The Gilded Ladle</span>
  </section>
</main>
</body>
</html>
```